Football blog needs a Wordpress design new site

We need a wordpress design for a new football blog site. We would like to see a design that uses the colours green, white and black and one that makes good use of the slideshow widgets as scene in the site 'www.kestrunpitch.net'
We would like a modern and sleek looking site but one that is also professional and easy to navigate.
Updates
Unfortunately due to unforeseen circumstances we are having to shorten the deadline date for this project.
The new deadline date is 16/07/2014.
We apologise for any inconveniance
Industry/Entity Type
It Professional
Look and feel
Each slider illustrates characteristics of the customer's brand and the style your logo design should communicate.

```html
<!DOCTYPE html>
<html lang="en">
<head>
<meta charset="utf-8">
<title>Kickoff Natter — Football Blog</title>
<link rel="stylesheet" href="https://fonts.googleapis.com/css2?family=Arimo:ital,wght@0,400;0,700;1,400&display=swap">
<style>
:root{
  --green:#3cb04a;
  --green-dark:#2f9a3c;
  --ink:#222;
  --text:#555;
  --muted:#888;
  --line:#e2e2e2;
  --panel:#1f1f1f;
  --footer:#232323;
  --footer-box:#333;
  --white:#fff;
}
*{box-sizing:border-box;margin:0;padding:0}
html,body{width:997px;height:1200px;overflow:hidden;background:var(--white)}
body{position:relative;font-family:"Arimo",Arial,sans-serif;color:var(--text);font-size:8px}
.abs{position:absolute}
a{color:inherit;text-decoration:none}

/* top bar */
.topbar{left:0;top:0;width:997px;height:19px;background:#f4f4f4;border-bottom:1px solid var(--line)}
.toplinks{right:259px;top:0;height:19px;display:flex;gap:14px;align-items:center;font-size:7px;color:#555}
.login{left:690px;top:0;width:48px;height:19px;background:var(--green);color:var(--white);font-size:7px;font-weight:700;display:flex;align-items:center;justify-content:center}

/* header */
.brand{left:234px;top:40px;width:110px;height:74px;text-align:center}
.brand-dot{display:block;margin:0 auto 6px;width:44px;height:44px;border-radius:50%;background:var(--green)}
.brand-name{font-size:11px;color:var(--green);font-weight:400}
.search{left:532px;top:60px;width:96px;height:21px;border:1px solid var(--line);font-size:6px;font-style:italic;color:#aaa;padding:6px 7px}
.search-btn{left:627px;top:59px;width:22px;height:22px;border-radius:50%;background:var(--green)}

/* nav */
.nav{left:0;top:120px;width:997px;height:26px;border-top:1px solid var(--line);border-bottom:3px solid #e6e6e6}
.nav-item{top:129px;font-size:7px;color:#777;letter-spacing:.3px}
.nav-item.is-active{color:#333;font-weight:700}

/* slider */
.slide{top:152px;height:182px;overflow:hidden}
.slide .photo{position:absolute;inset:0}
.slide .caption{position:absolute;left:0;right:0;bottom:0;height:36px;background:rgba(0,0,0,.62);color:var(--white);font-weight:700;font-size:8px;line-height:10px;padding:8px 9px}
.slide-main .caption{font-weight:400;font-size:9px}
.slide-main .date{display:block;font-size:6px;margin-top:4px;font-weight:400}
.slide-arrows{right:6px;top:126px;display:flex;gap:2px}
.slide-arrows span{width:13px;height:13px;background:#333;display:block}

/* section headings */
.sec-title{font-size:9px;color:#555;text-transform:uppercase;letter-spacing:.2px}
.sec-rule{height:1px;background:var(--line)}
.sec-bar{height:3px;background:var(--green)}
.pager{display:flex;gap:3px}
.pager span{width:16px;height:11px;background:#ccc;display:block}

.thumb{display:block}
.card-title{font-size:7px;font-weight:700;color:#555;line-height:9px}

.tile{overflow:hidden}
.tile .photo{position:absolute;inset:0}
.tile .overlay{position:absolute;left:0;right:0;background:rgba(90,90,90,.72);color:var(--white);font-weight:700;font-size:7px;line-height:9px;padding:6px 7px}
.tile .overlay.center{text-align:center;font-size:9px;line-height:11px}

.post-title{font-size:7px;color:#444;line-height:9px}
.post-title.is-hot{color:var(--green)}
.post-meta{font-size:5.5px;color:#888}
.post-meta b{color:#1a8fc9;font-weight:400}

/* sidebar */
.side-title{font-size:9px;color:#333}
.social{border:1px solid var(--line)}
.social p{font-size:6px;color:#666;padding:6px 5px 5px}
.social-icons{display:flex;gap:2px;padding-left:5px}
.social-icons span{width:11px;height:11px;display:block}
.video{background:var(--panel);color:var(--white)}
.video h4{font-size:7px;padding:10px 9px 0}
.video .title{font-size:7px;font-weight:700;line-height:9px}
.video .desc{font-size:5.5px;color:#bbb;line-height:7px}
.read-more{background:var(--green);color:var(--white);font-size:6px;font-weight:700;display:flex;align-items:center;justify-content:center}
.promo{border:1px solid var(--line);background:#f4f4f4;text-align:center}
.promo-dot{display:block;margin:0 auto;width:26px;height:26px;border-radius:50%;background:var(--green)}
.promo-name{font-size:7px;color:var(--green);margin-top:3px}
.promo-head{font-size:13px;font-weight:700;color:#555;margin-top:4px;letter-spacing:.3px}
.promo-btn{display:flex;align-items:center;justify-content:center;margin:9px auto 0;width:107px;height:21px;border-radius:11px;background:var(--green);color:var(--white);font-size:7px;font-weight:700}
.widget{border:1px solid var(--line)}
.tabs{display:flex;border-bottom:1px solid var(--line);height:18px;font-size:6px}
.tabs span{flex:1;display:flex;align-items:center;justify-content:center;border-right:1px solid var(--line)}
.tabs span.is-active{background:var(--white);border-bottom:2px solid var(--white)}
.widget ul{list-style:none;padding:0 9px}
.widget li{font-size:6.5px;color:#666;height:21px;line-height:21px;border-bottom:1px solid #eee;padding-left:10px;position:relative}
.widget li::before{content:"";position:absolute;left:0;top:9px;width:4px;height:4px;border-radius:50%;background:#f0a400}
.widget li.is-hot{color:var(--green)}
.widget li:last-child{border-bottom:0}

/* footer */
.footer{left:0;top:964px;width:997px;height:236px;background:var(--footer)}
.foot-title{font-size:7px;font-weight:700;color:var(--white);letter-spacing:.2px}
.foot-rule{height:1px;background:#3a3a3a}
.subscribe{background:var(--footer-box)}
.subscribe p{font-size:6px;color:#bbb;line-height:8px;padding:11px 10px 0}
.sub-input{left:10px;top:33px;width:122px;height:19px;background:#555}
.sub-send{left:136px;top:33px;width:35px;height:19px;background:#777;color:var(--white);font-size:6px;display:flex;align-items:center;justify-content:center}
.sub-note{left:10px;top:55px;font-size:4.5px;color:#999}
.site-links{list-style:none;font-size:6px;color:#bbb;line-height:9px}
.site-links li::before{content:"» ";color:#777}
.post-w .thumb{background:#ddd;border:3px solid var(--white)}
.post-w h5{font-size:7px;color:#ddd}
.post-w h5.is-hot{color:var(--green)}
.post-w p{font-size:6px;color:#aaa;line-height:8px}
.foot-legal{left:233px;top:1154px;width:505px;text-align:center;font-size:5.5px;color:#bbb;line-height:8px}
</style>
</head>
<body>

<div class="abs topbar"></div>
<nav class="abs toplinks"><a>Home</a><a>Most Popular</a><a>Top Stories</a><a>Custom Links</a></nav>
<a class="abs login">LOGIN</a>

<div class="abs brand"><span class="brand-dot"></span><span class="brand-name">Kickoff Natter</span></div>
<div class="abs search">Search Keywords</div>
<svg class="abs search-btn" viewBox="0 0 22 22" aria-hidden="true"><circle cx="11" cy="11" r="11" fill="#3cb04a"/><circle cx="10" cy="10" r="3.5" fill="none" stroke="#fff" stroke-width="1.6"/><line x1="12.5" y1="12.5" x2="16" y2="16" stroke="#fff" stroke-width="1.8"/></svg>

<div class="abs nav"></div>
<a class="abs nav-item" style="left:233px">ARTICLE</a>
<a class="abs nav-item" style="left:280px">BLOGS</a>
<a class="abs nav-item is-active" style="left:323px">PHOTOS</a>
<a class="abs nav-item" style="left:372px">VIDEOS</a>
<a class="abs nav-item" style="left:421px">USEFUL LINK</a>
<a class="abs nav-item" style="left:481px">LINKS</a>

<!-- slider -->
<article class="abs slide" style="left:52px;width:172px">
  <div class="photo" role="img" aria-label="Photo of two young fans outdoors" style="background:linear-gradient(135deg,#6b5a4a,#3a3230 60%,#8a6a5a)"></div>
  <div class="caption">Lorem Ipsum is simply dummy text of the printing</div>
</article>
<article class="abs slide slide-main" style="left:233px;width:325px">
  <div class="photo" role="img" aria-label="Photo of a footballer striking a ball in a splash of water" style="background:radial-gradient(circle at 25% 30%,#6a9ac8,#1a3a6a 45%,#0a1428)"></div>
  <div class="abs slide-arrows"><span></span><span></span></div>
  <div class="caption">Lorem Ipsum is simply dummy text of the printing and typesetting<span class="date">◷ 29 July 2014</span></div>
</article>
<article class="abs slide" style="left:565px;width:173px">
  <div class="photo" role="img" aria-label="Photo of a desk with a leather bag, notebook and glass" style="background:linear-gradient(160deg,#8a5030,#4a3020 50%,#c8c0b0)"></div>
  <div class="caption">Lorem Ipsum is simply dummy text of the printing and typesetting industry</div>
</article>
<article class="abs slide" style="left:746px;width:173px">
  <div class="photo" role="img" aria-label="Black and white photo of a city street with tall buildings" style="background:linear-gradient(180deg,#9a9a9a,#3a3a3a 60%,#1a1a1a)"></div>
  <div class="caption">Lorem Ipsum is simply dummy</div>
</article>

<!-- recommended -->
<h3 class="abs sec-title" style="left:233px;top:362px">Recommended for you</h3>
<div class="abs sec-rule" style="left:233px;top:379px;width:351px"></div>
<div class="abs sec-bar" style="left:233px;top:377px;width:98px"></div>
<div class="abs pager" style="left:548px;top:364px"><span></span><span></span></div>

<div class="abs thumb" role="img" aria-label="Photo of a city street" style="left:233px;top:388px;width:110px;height:70px;background:linear-gradient(180deg,#8a8a8a,#2a2a2a)"></div>
<div class="abs thumb" role="img" aria-label="Photo of two young fans" style="left:353px;top:388px;width:110px;height:70px;background:linear-gradient(135deg,#7a6050,#3a3030 60%,#b04040)"></div>
<div class="abs thumb" role="img" aria-label="Photo of a person in a printed t-shirt" style="left:473px;top:388px;width:110px;height:70px;background:linear-gradient(135deg,#c89060,#e8e0d8 55%,#b07040)"></div>
<p class="abs card-title" style="left:233px;top:460px;width:110px">Lorem Ipsum is simply dummy text of the printing and typesetting industry</p>
<p class="abs card-title" style="left:353px;top:460px;width:110px">Lorem Ipsum is simply dummy text of the printing</p>
<p class="abs card-title" style="left:473px;top:460px;width:110px">Lorem Ipsum is simply dummy text of the printing</p>

<!-- hot list grid -->
<h3 class="abs sec-title" style="left:233px;top:510px">Hot list</h3>
<div class="abs sec-rule" style="left:233px;top:526px;width:351px"></div>
<div class="abs sec-bar" style="left:233px;top:524px;width:50px"></div>
<div class="abs pager" style="left:548px;top:511px"><span></span><span></span></div>

<article class="abs tile" style="left:233px;top:533px;width:200px;height:92px">
  <div class="photo" role="img" aria-label="Photo of light bulbs and circuit parts" style="background:radial-gradient(circle at 70% 30%,#d8c840,#9a9a90 35%,#6a6a66)"></div>
  <div class="overlay center" style="top:52px;background:none;font-size:9px">Lorem Ipsum is simply dummy text of the printing</div>
</article>
<article class="abs tile" style="left:442px;top:533px;width:142px;height:92px">
  <div class="photo" role="img" aria-label="Illustration of a figure dissolving into blue particles" style="background:linear-gradient(135deg,#2a6aa8,#e8eef4 55%,#8a9aa8)"></div>
  <div class="overlay" style="top:56px;left:6px;right:6px">Lorem Ipsum is simply dummy text of the printing</div>
</article>
<article class="abs tile" style="left:233px;top:632px;width:143px;height:92px">
  <div class="photo" role="img" aria-label="Illustration of a figure dissolving into blue particles" style="background:linear-gradient(135deg,#e8eef4,#2a6aa8 55%,#8a9aa8)"></div>
  <div class="overlay" style="top:59px;right:0">Lorem Ipsum is simply dummy text of the printing</div>
</article>
<article class="abs tile" style="left:384px;top:632px;width:200px;height:92px">
  <div class="photo" role="img" aria-label="Photo of light bulbs and circuit parts" style="background:radial-gradient(circle at 30% 30%,#d8c840,#9a9a90 35%,#6a6a66)"></div>
  <div class="overlay center" style="top:54px;background:none">Lorem Ipsum is simply dummy text of the printing</div>
</article>

<!-- hot list posts -->
<h3 class="abs sec-title" style="left:233px;top:753px">Hot list</h3>
<div class="abs sec-rule" style="left:233px;top:769px;width:351px"></div>
<div class="abs sec-bar" style="left:233px;top:767px;width:50px"></div>
<div class="abs pager" style="left:548px;top:755px"><span></span><span></span></div>

<div class="abs thumb" role="img" aria-label="Illustration of a DNA strand" style="left:233px;top:777px;width:110px;height:58px;background:linear-gradient(135deg,#0a3a3a,#1a8a8a 50%,#0a2a30)"></div>
<div class="abs thumb" role="img" aria-label="Photo of a stethoscope on an open book" style="left:350px;top:777px;width:115px;height:58px;background:linear-gradient(180deg,#6a8ac8,#c8d8e8 60%,#3a4a6a)"></div>
<div class="abs thumb" role="img" aria-label="Photo of a person with a dog in a meadow" style="left:473px;top:777px;width:111px;height:58px;background:linear-gradient(160deg,#e8d8a0,#b8c860 60%,#8aa040)"></div>
<p class="abs post-title" style="left:233px;top:844px;width:115px">Who Says The Waves Aren't Better On The Other Side!</p>
<p class="abs post-title" style="left:350px;top:844px;width:115px">Who Says The Waves Aren't Better On The Other Side!</p>
<p class="abs post-title is-hot" style="left:484px;top:844px;width:115px">Who Says The Waves Aren't Better On The Other Side!</p>
<p class="abs post-meta" style="left:233px;top:868px">◷ 12 May 2014 | <b>4 Replies</b></p>
<p class="abs post-meta" style="left:350px;top:868px">◷ 12 May 2014 | <b>4 Replies</b></p>
<p class="abs post-meta" style="left:484px;top:868px">◷ 12 May 2014 | <b>4 Replies</b></p>

<!-- sidebar -->
<h3 class="abs side-title" style="left:599px;top:362px">Social Media</h3>
<div class="abs social" style="left:599px;top:377px;width:139px;height:40px">
  <p>Connect with us on the following social media.</p>
  <div class="social-icons">
    <span style="background:#f08a20"></span><span style="background:#3b5998"></span><span style="background:#33a8e0"></span><span style="background:#c8232c"></span><span style="background:#555"></span><span style="background:#d03a8a"></span><span style="background:#0a70a8"></span><span style="background:#c0302a"></span>
  </div>
</div>

<section class="abs video" style="left:599px;top:436px;width:139px;height:188px">
  <h4>VIDEO GALLERY</h4>
  <div class="abs" role="img" aria-label="Photo of a woman raising her arms by the sea" style="left:9px;top:25px;width:121px;height:68px;background:linear-gradient(180deg,#6ab0e0,#d8eef8 55%,#c8b8a0)"></div>
  <p class="abs title" style="left:9px;top:101px;width:121px">Lorem Ipsum is simply dummy text of the printing and typesetting</p>
  <p class="abs desc" style="left:9px;top:122px;width:121px">Lorem Ipsum is simply dummy text of the printing and typesetting industry. Lorem Ipsum has been the industry's standard dummy text ever since</p>
  <div class="abs" style="left:9px;top:159px;width:121px;height:1px;background:#3a3a3a"></div>
  <a class="abs read-more" style="left:81px;top:160px;width:44px;height:14px">READ MORE</a>
</section>

<section class="abs promo" style="left:599px;top:642px;width:139px;height:121px">
  <div style="padding-top:16px"><span class="promo-dot"></span></div>
  <p class="promo-name">Kickoff Natter</p>
  <p class="promo-head">WATCH UNLIMITED</p>
  <a class="promo-btn">START YOUR FREE TRIAL</a>
</section>

<h3 class="abs side-title" style="left:599px;top:789px;font-size:7px">WIDGET LIST</h3>
<div class="abs sec-rule" style="left:599px;top:802px;width:139px"></div>
<section class="abs widget" style="left:599px;top:804px;width:139px;height:127px">
  <div class="tabs"><span class="is-active">Popular</span><span>Recent</span><span style="border-right:0">Archieve</span></div>
  <ul>
    <li>This 3-Year-Old Skates Better Than</li>
    <li>This Is How You Exit The Highway...</li>
    <li>10 DIY Life Hacks for Camping</li>
    <li class="is-hot">This 3-Year-Old Skates</li>
    <li>Old Skates Better Than Most Teens!</li>
  </ul>
</section>

<!-- footer -->
<footer class="abs footer"></footer>
<h4 class="abs foot-title" style="left:233px;top:992px">SUBSCRIBE</h4>
<div class="abs subscribe" style="left:233px;top:1008px;width:184px;height:72px">
  <p>Enter your email address below to receive updates each time we publish new content.</p>
  <div class="abs sub-input"><svg width="18" height="12" viewBox="0 0 18 12" style="margin:4px 5px" aria-hidden="true"><rect x=".5" y=".5" width="15" height="10" fill="none" stroke="#ddd"/><path d="M.5 .5 8 6 15.5 .5" fill="none" stroke="#ddd"/></svg></div>
  <div class="abs sub-send">SEND</div>
  <p class="abs sub-note">Privacy guaranteed. We never share your info.</p>
</div>

<h4 class="abs foot-title" style="left:458px;top:992px">SITE INFO</h4>
<div class="abs foot-rule" style="left:458px;top:1004px;width:74px"></div>
<ul class="abs site-links" style="left:458px;top:1016px">
  <li>Log In</li><li>My Account</li><li>Blog Post</li><li>Video</li><li>Entire RSS</li>
</ul>

<h4 class="abs foot-title" style="left:580px;top:992px">POST WIDGET</h4>
<div class="abs foot-rule" style="left:580px;top:1004px;width:158px"></div>
<div class="abs post-w" style="left:580px;top:1015px;width:158px">
  <div class="abs thumb" role="img" aria-label="Screenshot thumbnail of a post" style="left:0;top:0;width:42px;height:40px"></div>
  <h5 class="abs" style="left:50px;top:2px">Lorem Ipsum is simply dummy</h5>
  <p class="abs" style="left:50px;top:14px;width:108px">Lorem Ipsum is simply dummy text of the printing and typesetting industry.</p>
</div>
<div class="abs foot-rule" style="left:580px;top:1063px;width:158px;background:#555"></div>
<div class="abs post-w" style="left:580px;top:1071px;width:158px">
  <div class="abs thumb" role="img" aria-label="Screenshot thumbnail of a post" style="left:0;top:0;width:42px;height:40px"></div>
  <h5 class="abs is-hot" style="left:50px;top:2px">Lorem Ipsum is simply dummy</h5>
  <p class="abs" style="left:50px;top:14px;width:108px">Lorem Ipsum is simply dummy text of the printing and typesetting industry.</p>
</div>

<div class="abs foot-rule" style="left:233px;top:1134px;width:505px"></div>
<div class="abs foot-legal">
  <p>Lorem Ipsum is simply dummy text of the printing and typesetting industry. Lorem Ipsum has been the industry's standard dummy text ever since the 1500s, when an unknown printer took a galley of type and scrambled it to make a type specimen book.</p>
  <p style="margin-top:6px">© 2014 Company Name. All rights reserved.</p>
</div>

</body>
</html>
```